Real Estate Acquisition Company Needs Business Card Design

Bellwick Real Estate is in need of a business card design!

As a Real Estate Acquisition Company, Bellwick Real Estate conducts mutually beneficial real estate transactions that actively consider the needs of the seller. At Bellwick Real Estate we’re actively buying properties from those that see value in a direct transaction, but more importantly want reassurances that they, personally, are in integral part of it. Of course, it all starts with fair market value, but it doesn’t stop there. We’ve found the most success when we offer more. And with our deep experience in this industry, we’ve discovered that we have a lot to offer!

We already have a logo and brand guidelines that we've uploaded. Our final design should stay true to the guidelines. We are looking for a business card design that has two names (Ex. Jane Doe & John Doe) and contact information for each person- this way the company principals can share a card as they often do business as a team.
Updates

The criteria was unfortunately not met on most designs. We are looking for a card that has a layout for TWO names and respective contact information for each of the two people. Almost all designs only had a space for one name and one set of contact information.

Industry/Entity Type

Real Estate

Contact Information for Business Card

We are looking for a business card design that has two names (Ex. Jane Doe & John Doe) and each of their contact information- this way the company principals can share a card as they often do business as a team.

Font styles to use
Other font styles liked:
• Use Brand Guidelines

Requirements
Must have
• Please stay true to our Brand Guidelines for colours, fonts, and positioning of logo.

We require a layout for two names and respective contact information. The company principals work as a team and want a card that has both their information on it.

```html
<!DOCTYPE html>
<html lang="en">
<head>
<meta charset="utf-8">
<title>Bellwick Real Estate – Business Card</title>
<link href="https://fonts.googleapis.com/css2?family=Montserrat:wght@400;500;600&display=swap" rel="stylesheet">
<style>
  :root{
    --navy:#13213a;
    --gold:#f0ab2b;
    --white:#ffffff;
    --backdrop:#2a2c30;
    --muted:#dfe3ea;
  }
  *{margin:0;padding:0;box-sizing:border-box}
  html,body{width:1200px;height:900px;overflow:hidden;background:var(--backdrop)}
  body{font-family:"Montserrat",sans-serif;position:relative}
  .card{position:absolute;left:250px;width:700px;height:400px;background:var(--navy);overflow:hidden;border-radius:4px}
  .card--logo{top:30px}
  .card--contact{top:470px}

  .card--logo .brand{position:absolute;inset:0;display:flex;align-items:center;justify-content:center;gap:16px}
  .brand__dot{width:22px;height:22px;border-radius:50%;background:var(--gold)}
  .brand__name{font-weight:600;letter-spacing:3px;text-transform:uppercase;white-space:nowrap}
  .card--logo .brand__name{color:var(--white);font-size:38px}

  .band{position:absolute;left:0;top:0;width:700px;height:175px}
  .card--contact .brand{position:absolute;left:0;top:0;width:700px;height:150px;display:flex;align-items:center;justify-content:center;gap:14px}
  .card--contact .brand__name{color:var(--navy);font-size:32px}
  .card--contact .brand__dot{width:18px;height:18px}

  .person{position:absolute;color:var(--white)}
  .person--one{left:40px;top:192px}
  .person--two{left:400px;top:205px}
  .person__name{font-size:17px;font-weight:600;letter-spacing:1.5px;text-transform:uppercase}
  .person__role{font-size:12px;color:var(--gold);margin-top:2px;margin-bottom:14px}
  .contact{display:flex;align-items:center;gap:10px;font-size:14px;margin-bottom:9px;color:var(--muted)}
  .contact__icon{width:24px;height:24px;flex:none}
  .website{position:absolute;left:40px;bottom:28px;color:var(--muted);font-size:15px;letter-spacing:.5px}
  .divider{position:absolute;left:0;top:0}
</style>
</head>
<body>

<section class="card card--logo">
  <div class="brand">
    <span class="brand__dot"></span>
    <span class="brand__name">Bellwick Real Estate</span>
  </div>
</section>

<section class="card card--contact">
  <svg class="band" viewBox="0 0 700 175" width="700" height="175" aria-hidden="true">
    <polygon points="0,0 700,0 700,168 0,140" fill="#ffffff"/>
    <line x1="0" y1="140" x2="700" y2="168" stroke="#f0ab2b" stroke-width="2.5"/>
  </svg>
  <div class="brand">
    <span class="brand__dot"></span>
    <span class="brand__name">Bellwick Real Estate</span>
  </div>

  <svg class="divider" viewBox="0 0 700 400" width="700" height="400" aria-hidden="true">
    <line x1="372" y1="215" x2="342" y2="370" stroke="#f0ab2b" stroke-width="1.2" opacity=".8"/>
  </svg>

  <div class="person person--one">
    <p class="person__name">Rowan Hale</p>
    <p class="person__role">Director and ceo</p>
    <p class="contact">
      <svg class="contact__icon" viewBox="0 0 24 24" aria-hidden="true"><rect x="1" y="1" width="22" height="22" rx="5" fill="none" stroke="#f0ab2b" stroke-width="1.5"/><path d="M8.5 6.5l2 2.5-1.3 1.3a7 7 0 0 0 4.5 4.5l1.3-1.3 2.5 2-1.3 2c-4.8-.2-9-4.4-9.2-9.2z" fill="#fff"/></svg>
      +555 201 4478
    </p>
    <p class="contact">
      <svg class="contact__icon" viewBox="0 0 24 24" aria-hidden="true"><rect x="1" y="1" width="22" height="22" rx="5" fill="none" stroke="#f0ab2b" stroke-width="1.5"/><rect x="6" y="8" width="12" height="8.5" fill="#fff"/><path d="M6 8l6 5 6-5M6 16.5l4.5-4.2M18 16.5l-4.5-4.2" fill="none" stroke="#13213a" stroke-width="1"/></svg>
      rowan@bellwick.com
    </p>
  </div>

  <div class="person person--two">
    <p class="person__name">Rowan Hale</p>
    <p class="person__role">Director and ceo</p>
    <p class="contact">
      <svg class="contact__icon" viewBox="0 0 24 24" aria-hidden="true"><rect x="1" y="1" width="22" height="22" rx="5" fill="none" stroke="#f0ab2b" stroke-width="1.5"/><path d="M8.5 6.5l2 2.5-1.3 1.3a7 7 0 0 0 4.5 4.5l1.3-1.3 2.5 2-1.3 2c-4.8-.2-9-4.4-9.2-9.2z" fill="#fff"/></svg>
      +555 201 4478
    </p>
    <p class="contact">
      <svg class="contact__icon" viewBox="0 0 24 24" aria-hidden="true"><rect x="1" y="1" width="22" height="22" rx="5" fill="none" stroke="#f0ab2b" stroke-width="1.5"/><rect x="6" y="8" width="12" height="8.5" fill="#fff"/><path d="M6 8l6 5 6-5M6 16.5l4.5-4.2M18 16.5l-4.5-4.2" fill="none" stroke="#13213a" stroke-width="1"/></svg>
      rowan@bellwick.com
    </p>
  </div>

  <p class="website">www.bellwick.com</p>
</section>

</body>
</html>
```